Upscale neighbourhood mail campaign requiring 3 postcard designs

I am looking for a series of 3 postcards to be designed. They all must have a common look to them to show they belong to the same company. We are a local real estate company that specializes in an area called Ashvale Ridge. You can visit our website at www.ashvaleridgehomes.ca to have a peek. I have HD photos I can provide of the area, or include your own ideas/images. The post cards text will be provided and they will be sent as unaddressed admail, meaning there is no need to include areas for postage or mailing addresses. The final design should be clean, recognizable and professional. These cards must have visual impact on the recipients.

COPY for 3 POSTCARDs

POSTCARD 1

FRONT

(included Logo)

Get noticed.
Your home deserves it

BACK

We take finding Buyers for your home very seriously.

Through our unique, Ashvale Ridge specific website, targeted digital marketing, EXCLUSIVE Buyer incentives and our featured listing promotion, your home is in front of the people that want to see it. People who WANT to live in Ashvale Ridge.

Visit ashvaleridgehomes.ca to learn more about what we do so your home can GET NOTICED. Your home deserves it.

Colet Varnish- PREC | Pelham Estates LTD | 604-555-0192 | homes@varnish.ca

This communication is not intended to cause or induce breach of an existing agency agreement. Although this information has been received from sources deemed reliable, we assume no responsibility for its accuracy and without offering advice, make this submission to prior sale or lease, change in price or terms, and withdrawal without notice

POSTCARD 2

FRONT

Logo

Get noticed.
Expect the best.

BACK

You deserve the best when it comes to the marketing and exposure of your home, which is why your neighbours choose ashvaleridgehomes.ca to sell their home. Our award winning results combined with our systematized approach to marketing makes selling your home with us a breeze. In addition, you have full access to our dedicated client concierge, in place to ensure your sale is stress free and an overall rewarding experience.

Visit ashvaleridgehomes.ca to learn more about what we do so your home can GET NOTICED. Expect the best.

POSTCARD 3

FRONT

Logo

Get noticed.
Rule the web

BACK

No one promotes your home more than ashvaleridgehomes.ca. Just try us. Type ashvale ridge homes into any internet search browser and see for yourself. We advertise Ashvale Ridge internationally, in all major Canadian Cities and locally to affluent Buyers who appreciate what Ashvale Ridge has to offer. No one offers a more specific, targeted approach to getting your home sold.

Visit ashvaleridgehomes.ca to learn more about what we do so your home can GET NOTICED so you can rule the web.

Target Market(s)

Upscale neighbourhood in Surrey BC, Canada called Ashvale Ridge

Industry/Entity Type

Real Estate

Font styles to use
Other font styles liked:
• Lato

Colors

Designer to choose colors to be used in the design.

Requirements
Must have
• -Clean, impactful and professional looking card
• -Font- Lato
• -Provided Ashvale Ridge Homes logo
• -Check www.ashvaleridgehomes.ca for complimentary color scheme
• -provided Ashvale Ridge logo on the front
• -provided --CV logo, Pelham Estates logo and medallion crest on the back
• -Disclaimer in small, low-key font/color - "This communication is not intended to cause or induce breach of an existing agency agreement. Although this information has been received from sources deemed reliable, we assume no responsibility for its accuracy and without offering advice, make this submission to prior sale or lease, change in price or terms, and withdrawal without notice"
Nice to have
• -bold images, not 100% necessary though (discretion of designer)
• -impactful front of postcard
Should not have
• -cartoon style drawings
• -areas for postage or mailing addresses (this will be sent as non addressed admail by the local postal courier)

```html
<!DOCTYPE html>
<html lang="en">
<head>
<meta charset="utf-8">
<title>Ashvale Ridge Homes – Postcard</title>
<link rel="stylesheet" href="https://fonts.googleapis.com/css2?family=Lato:ital,wght@0,400;0,700;0,900;1,400&display=swap">
<style>
  :root {
    --olive: #5b6b2f;
    --olive-dark: #4a5826;
    --olive-text: #5a6a2c;
    --grey-panel: #dcdcdc;
    --ink: #1d1d1d;
    --body-grey: #3a3a3a;
    --paper: #ffffff;
    --backdrop: #e9e7e3;
  }
  * { box-sizing: border-box; margin: 0; padding: 0; }
  html, body { width: 860px; height: 1200px; overflow: hidden; }
  body {
    background: var(--backdrop);
    font-family: "Lato", Arial, sans-serif;
    color: var(--ink);
    position: relative;
  }
  .postcard {
    position: absolute;
    left: 30px;
    width: 800px;
    height: 514px;
    background: var(--paper);
    overflow: hidden;
    box-shadow: 0 2px 8px rgba(0,0,0,.18);
  }
  .postcard--front { top: 40px; }
  .postcard--back { top: 626px; }

  /* FRONT */
  .front-photo { position: absolute; inset: 0; width: 800px; height: 514px; }
  .brand {
    display: flex; align-items: center; justify-content: center; gap: 8px;
    font-weight: 700;
    color: var(--ink);
    letter-spacing: .6px;
    text-transform: uppercase;
    white-space: nowrap;
  }
  .brand__mark { width: 12px; height: 12px; background: var(--ink); flex: none; }
  .front-brand { position: absolute; left: 24px; top: 62px; font-size: 16px; }
  .front-tagline { position: absolute; right: 20px; bottom: 20px; text-align: right; }
  .front-tagline__headline {
    font-size: 46px; font-weight: 900; color: var(--olive-text); line-height: 1; letter-spacing: -.5px;
  }
  .front-tagline__sub { font-size: 16px; font-style: italic; color: var(--ink); margin-top: 6px; }

  /* BACK */
  .back-shapes { position: absolute; inset: 0; width: 800px; height: 514px; }
  .back-headline {
    position: absolute; left: 24px; top: 32px;
    font-size: 33px; font-weight: 900; line-height: 1.14;
    color: var(--olive-text); letter-spacing: -.3px;
  }
  .pitch {
    position: absolute; left: 0; top: 170px; width: 444px; height: 344px;
    background: var(--olive);
    color: #fff;
    padding: 28px 36px 0 24px;
  }
  .pitch__body { font-size: 14.5px; line-height: 1.32; }
  .pitch__body + .pitch__body { margin-top: 16px; }
  .pitch strong { font-weight: 700; }
  .pitch__contact { font-size: 11px; font-weight: 700; margin-top: 14px; white-space: nowrap; letter-spacing: -.1px; }
  .disclaimer {
    margin-top: 20px;
    background: var(--olive-dark);
    border-radius: 14px;
    padding: 10px 20px;
    font-size: 10px; line-height: 1.38; color: #e6e9dc;
    width: 400px;
  }
  .testimonial { position: absolute; left: 470px; top: 52px; width: 302px; }
  .testimonial__quote {
    font-size: 14px; line-height: 1.46; color: var(--body-grey);
    text-align: justify; padding-left: 24px; position: relative;
  }
  .testimonial__mark {
    position: absolute; font-family: Georgia, serif; font-weight: 700;
    font-size: 38px; color: var(--olive-text); line-height: 1;
  }
  .testimonial__mark--open { left: 0; top: -8px; }
  .testimonial__mark--close { right: -8px; bottom: -22px; }
  .testimonial__name {
    text-align: right; margin-top: 16px; font-size: 15px; color: var(--olive-text); letter-spacing: .3px;
  }
  .back-signoff {
    position: absolute; left: 540px; top: 388px; width: 250px;
    display: flex; flex-direction: column; align-items: center; gap: 16px;
  }
  .back-brand { font-size: 15px; }
  .partners { display: flex; align-items: center; gap: 12px; }
  .partners__name { font-size: 12px; font-weight: 700; color: var(--ink); text-transform: uppercase; line-height: 1.1; }
  .partners__badge { width: 42px; height: 42px; border-radius: 50%; background: #2a2a2a; }
  .partners__tile { width: 52px; height: 40px; background: #2c4f94; }
</style>
</head>
<body>

<section class="postcard postcard--front" aria-label="Postcard front">
  <svg class="front-photo" viewBox="0 0 800 514" role="img" aria-label="Photograph of a large stone-clad luxury home with landscaped front lawn and driveway">
    <defs>
      <linearGradient id="photo-tone" x1="0" y1="0" x2="0" y2="1">
        <stop offset="0" stop-color="#a9c6e6"/>
        <stop offset="0.45" stop-color="#9b9c9c"/>
        <stop offset="0.7" stop-color="#6f9a3a"/>
        <stop offset="1" stop-color="#8f8c86"/>
      </linearGradient>
    </defs>
    <polygon points="0,137 800,0 800,375 0,514" fill="url(#photo-tone)"/>
  </svg>
  <div class="brand front-brand"><span class="brand__mark"></span>Ashvale Ridge Homes</div>
  <div class="front-tagline">
    <p class="front-tagline__headline">Get noticed</p>
    <p class="front-tagline__sub">Your home deserves it</p>
  </div>
</section>

<section class="postcard postcard--back" aria-label="Postcard back">
  <svg class="back-shapes" viewBox="0 0 800 514" aria-hidden="true">
    <polygon points="451,0 800,0 800,322 443,242 390,170" fill="var(--grey-panel)"/>
  </svg>

  <h1 class="back-headline">We take finding Buyers<br>for your home<br>very seriously.</h1>

  <div class="testimonial">
    <p class="testimonial__quote">
      <span class="testimonial__mark testimonial__mark--open">&ldquo;</span>Colet Varnish is an amazing realtor, so professional and friendly. A person that you can trust. Did not rest until he helped us find the house we wanted. This is our fourth time working with Colet, and we keep on coming back for his amazing and wonderful services. Thank you for everything Colet.<span class="testimonial__mark testimonial__mark--close">&rdquo;</span>
    </p>
    <p class="testimonial__name">RAY DELMONT</p>
  </div>

  <div class="pitch">
    <p class="pitch__body">Through our unique, Ashvale Ridge specific website, targeted digital marketing, <strong>EXCLUSIVE</strong> Buyer incentives and our featured listing promotion, your home is in front of the people that want to see it. People who WANT to live in Ashvale Ridge.</p>
    <p class="pitch__body">Visit <strong>ashvaleridgehomes.ca</strong> to learn more about<br>what we do so your home can <strong>GET NOTICED</strong>.<br>Your home deserves it.</p>
    <p class="pitch__contact">Colet Varnish- PREC | Pelham Estates LTD | 604-555-0192 | homes@varnish.ca</p>
    <p class="disclaimer">This communication is not intended to cause or induce breach of an existing agency agreement. Although this information has been received from sources deemed reliable, we assume no responsibility for its accuracy and without offering advice, make this submission to prior sale or lease, change in price or terms, and withdrawal without notice.</p>
  </div>

  <div class="back-signoff">
    <div class="brand back-brand"><span class="brand__mark"></span>Ashvale Ridge Homes</div>
    <div class="partners">
      <span class="partners__name">Pelham<br>Estates</span>
      <span class="partners__badge" role="img" aria-label="Partner medallion"></span>
      <span class="partners__tile" role="img" aria-label="Agent badge"></span>
    </div>
  </div>
</section>

</body>
</html>
```